Book Cover: Quiet Harbor: Small Ceremonies For The Restless Soul

I would like a full cover spread- front, back and spine as well as a stand alone front cover for Kindle for the book. Design a cover that mirrors the profound depth and dynamic energy of 'Quiet Harbor.' Envision a visual tapestry that draws readers into a transformative journey, where spirituality and self-care unite. Explore vibrant colors, intricate textures, and a sense of inner radiance that beckons readers to explore the book's rich wisdom within. See images for design inspiration attached. Even though some of the images are cartoon, I'd like the cover to be more serious than playful and very elegant.

About this book (back cover copy)
Are you ready to embark on a transformative journey and elevate your daily existence? "Quiet Harbor" is a treasure trove of practical yet profound rituals and wisdom from renowned self-care, healing, and spirituality experts.

Within these pages, you'll uncover a tapestry of guidance and insight from some of the world's most respected mentors. Their collective wisdom is your key to creating a sacred sanctuary within your everyday life.

From invigorating morning rituals to meditative practices, empowering affirmations, and transformative energy healing, you'll find a rich tapestry of tools to nurture a deeper connection with yourself and the universe.

Whether you're a seasoned practitioner or a newcomer to the world of self-care and spirituality, "Quiet Harbor" is your trusted companion on the journey to transform your life and elevate your daily experience. Open this book today and start your sacred, fulfilling adventure.

Colors
0094D4
00A9DD
6FCCEA
C7EBF8
E9F6FB
E54698
E96AAD
F1A4CE
F9D9EA
FCEFF6
6B429C
8869AF
B7A5CE
E3DAEB
F3F0F8

Requirements
Must have
• Title: Quiet Harbor: Subtitle: Small Ceremonies For The Restless Soul Name of Publisher: Lantern Bough Publishing- Logo on the back Back cover copy

```html
<!DOCTYPE html>
<html lang="en">
<head>
<meta charset="utf-8">
<title>Quiet Harbor – Full Cover Spread</title>
<link rel="stylesheet" href="https://fonts.googleapis.com/css2?family=Allison&family=Arimo:ital,wght@0,400;0,700;1,400&family=Cinzel:wght@400&family=Cormorant+Garamond:wght@500&display=swap">
<style>
  :root {
    --stage: #6b6b6b;
    --night: #07081c;
    --deep-blue: #0f1d45;
    --teal: #1d5f70;
    --sky-glow: #c7ebf8;
    --aqua: #6fccea;
    --violet: #6b429c;
    --rose: #e54698;
    --ember: #c46a3a;
    --gold-dark: #a9772a;
    --gold-light: #f4d98a;
    --gold-mid: #d3a347;
    --ink-light: #f3f0f8;
    --spine-gold: #f1d75a;
  }
  * { box-sizing: border-box; margin: 0; padding: 0; }
  html, body { width: 1200px; height: 1200px; overflow: hidden; }
  body { background: var(--stage); position: relative; font-family: "Arimo", Arial, sans-serif; }

  .spread {
    position: absolute; left: 50px; top: 210px;
    width: 1100px; height: 781px;
    display: flex; overflow: hidden;
    background: var(--night);
  }

  .gold-script {
    font-family: "Allison", cursive;
    font-weight: 400;
    background: linear-gradient(100deg, var(--gold-dark) 0%, var(--gold-light) 35%, var(--gold-mid) 60%, var(--gold-light) 80%, var(--gold-dark) 100%);
    -webkit-background-clip: text; background-clip: text;
    color: transparent;
    line-height: 1;
  }

  /* Back cover */
  .back-cover {
    position: relative; width: 525px; height: 100%;
    background:
      radial-gradient(ellipse 70% 18% at 30% 48%, rgba(196,106,58,0.35), transparent 70%),
      linear-gradient(180deg, var(--teal) 0%, #173d66 22%, var(--deep-blue) 42%, #111838 58%, var(--night) 75%);
    text-align: center; color: var(--ink-light);
  }
  .back-title { position: absolute; top: 44px; left: 0; width: 100%; font-size: 112px; }
  .back-subtitle {
    position: absolute; top: 186px; left: 0; width: 100%;
    font-family: "Cinzel", serif; font-size: 17.5px; letter-spacing: 0.4px; color: var(--ink-light);
  }
  .back-copy { position: absolute; top: 228px; left: 42px; width: 441px; font-size: 13.6px; line-height: 20.4px; }
  .back-copy p + p { margin-top: 20.4px; }
  .back-copy strong { font-weight: 700; }
  .publisher-mark {
    position: absolute; top: 688px; left: 21px; width: 220px;
    font-family: "Cormorant Garamond", serif; font-weight: 500;
    color: var(--ink-light); text-align: center;
  }
  .publisher-mark span { display: block; white-space: nowrap; }
  .publisher-mark .publisher-name { font-size: 24px; line-height: 30px; }
  .publisher-mark .publisher-word { font-size: 19px; line-height: 30px; letter-spacing: 3px; }

  /* Spine */
  .spine {
    position: relative; width: 49px; height: 100%;
    background: linear-gradient(180deg, #163a5a 0%, var(--deep-blue) 35%, var(--night) 70%);
    display: flex; flex-direction: column; align-items: center; padding-top: 34px;
  }
  .spine > * { writing-mode: vertical-rl; white-space: nowrap; }
  .spine-title { font-size: 64px; line-height: 49px; }
  .spine-subtitle { margin-top: 14px; font-family: "Cinzel", serif; font-size: 13px; color: var(--ink-light); letter-spacing: 0.4px; }
  .spine-publisher { margin-top: 16px; font-size: 13px; color: var(--spine-gold); }
  .spine-publisher strong { font-weight: 700; }

  /* Front cover */
  .front-cover { position: relative; width: 526px; height: 100%; }
  .front-art {
    position: absolute; inset: 0;
    background:
      radial-gradient(ellipse 36% 30% at 58% 30%, rgba(233,246,251,0.95), rgba(199,235,248,0.6) 40%, transparent 75%),
      radial-gradient(ellipse 60% 14% at 50% 46%, rgba(229,70,152,0.45), transparent 70%),
      radial-gradient(ellipse 55% 16% at 45% 50%, rgba(196,106,58,0.45), transparent 70%),
      radial-gradient(ellipse 70% 40% at 60% 20%, rgba(0,169,221,0.55), transparent 75%),
      linear-gradient(180deg, #1e6a7a 0%, #2a8a8f 18%, #4b3f8a 44%, #1b1d4e 58%, var(--night) 72%);
  }
  .front-title { position: absolute; left: 0; width: 100%; text-align: center; }
  .front-title .line-one { display: block; font-size: 196px; margin-top: 360px; padding-left: 30px; }
  .front-title .line-two { display: block; font-size: 196px; margin-top: -60px; padding-left: 60px; }
  .front-subtitle {
    position: absolute; top: 742px; left: 0; width: 100%; text-align: center;
    font-family: "Cinzel", serif; font-size: 18.5px; letter-spacing: 0.4px; color: var(--ink-light);
  }
</style>
</head>
<body>
  <main class="spread">
    <section class="back-cover">
      <h2 class="back-title gold-script">Quiet Harbor</h2>
      <p class="back-subtitle">Small Ceremonies For The Restless Soul</p>
      <div class="back-copy">
        <p><strong>Are you ready to embark on a transformative journey and elevate your daily existence?</strong> <em>"Quiet Harbor"</em> is a treasure trove of practical yet profound rituals and wisdom from renowned self-care, healing, and spirituality experts.</p>
        <p>Within these pages, you'll uncover a tapestry of guidance and insight from some of the world's most respected mentors. Their collective wisdom is your key to creating a sacred sanctuary within your everyday life.</p>
        <p>From invigorating morning rituals to meditative practices, empowering affirmations, and transformative energy healing, you'll find a rich tapestry of tools to nurture a deeper connection with yourself and the universe.</p>
        <p>Whether you're a seasoned practitioner or a newcomer to the world of self-care and spirituality, "Quiet Harbor" is your trusted companion on the journey to transform your life and elevate your daily experience. Open this book today and start your sacred, fulfilling adventure.</p>
      </div>
      <p class="publisher-mark">
        <span class="publisher-name">Lantern Bough</span>
        <span class="publisher-word">Publishing</span>
      </p>
    </section>

    <section class="spine">
      <span class="spine-title gold-script">Quiet Harbor</span>
      <span class="spine-subtitle">Small Ceremonies For The Restless Soul</span>
      <span class="spine-publisher"><strong>Lantern Bough</strong> Publishing</span>
    </section>

    <section class="front-cover">
      <div class="front-art" role="img" aria-label="Painted illustration of a silhouetted woman seated in meditation beneath a glowing sky, surrounded by a swirl of colourful butterflies and clouds"></div>
      <h1 class="front-title gold-script">
        <span class="line-one">Quiet</span>
        <span class="line-two">Harbor</span>
      </h1>
      <p class="front-subtitle">Small Ceremonies For The Restless Soul</p>
    </section>
  </main>
</body>
</html>
```